eBook Cover_H. Lindqvist-Borna
Schnell und zuverlässoig,Änderungswünsche wurden umgehend ausgeführt. Vielen Dank für das tolle Cover zu meinem ersten Buch!
Zielgruppe
freie Roman-Autorin (Erstlingswerk)
Zielgruppe: Lesende (Erwachsene), Frauen
Charakterisierung: magisch-realistischer Familienroman, spielt im Europa der Jetzt-Zeit
Aufgabenstellung
Im ersten Schritt geht es um ein Cover für ein eBook, das aber bei Bedarf als Book on Demand gedruckt werden soll. Es wird daher später Anforderung bzgl. Dicke / Umfang des gedruckten Buches und einer Rückseite geben. Das gewählte Design soll dann dahingehend überarbeitet und finale Druckdaten zur Verfügung gestellt werden. Dies soll von vornherein berücksichtigt werden und im Preis enthalten sein.
Titel: Regen über Glas, Monde im Moos
Autorinnenname: Henrike Lindqvist-Borna
des weiteren auf dem Cover: Roman

```html
<!DOCTYPE html>
<html lang="de">
<head>
<meta charset="utf-8">
<title>Regen über Glas, Monde im Moos – Henrike Lindqvist-Borna</title>
<link rel="stylesheet" href="https://fonts.googleapis.com/css2?family=Oswald:wght@700&family=Open+Sans:wght@400&display=swap">
<style>
  :root {
    --backdrop: #dcdcdc;
    --paper: #ffffff;
    --ink: #5a5f66;
    --frame: #6a6f76;
    --green-light: #3fe83f;
    --green-mid: #22c922;
    --green-deep: #0b9a12;
    --roman: #ffffff;
  }
  html, body {
    margin: 0;
    padding: 0;
    width: 841px;
    height: 1200px;
    overflow: hidden;
    background: var(--backdrop);
  }
  .canvas {
    position: relative;
    width: 841px;
    height: 1200px;
  }
  .cover {
    position: absolute;
    left: 45px;
    top: 45px;
    width: 750px;
    height: 1108px;
    background: var(--paper);
    box-shadow: 6px 6px 8px rgba(0, 0, 0, 0.35);
    overflow: hidden;
  }
  .cover__art {
    position: absolute;
    left: 0;
    top: 0;
    width: 750px;
    height: 1108px;
  }
  .cover__author {
    position: absolute;
    left: 350px;
    top: 349px;
    width: 339px;
    height: 58px;
    box-sizing: border-box;
    border: 2px solid var(--frame);
    display: flex;
    align-items: center;
    justify-content: center;
    font-family: "Open Sans", sans-serif;
    font-size: 21px;
    letter-spacing: 0.3px;
    color: var(--ink);
    text-transform: uppercase;
    white-space: nowrap;
  }
  .cover__title {
    position: absolute;
    left: 278px;
    width: 470px;
    top: 482px;
    margin: 0;
    text-align: center;
    font-family: "Oswald", sans-serif;
    font-weight: 700;
    font-size: 56px;
    line-height: 73px;
    letter-spacing: 2px;
    color: var(--ink);
    text-transform: uppercase;
  }
  .cover__title span { display: block; white-space: nowrap; }
  .cover__genre {
    position: absolute;
    left: 84px;
    top: 1040px;
    margin: 0;
    font-family: "Oswald", sans-serif;
    font-weight: 700;
    font-size: 52px;
    line-height: 1;
    letter-spacing: 1px;
    color: var(--roman);
    text-transform: uppercase;
  }
</style>
</head>
<body>
  <div class="canvas">
    <div class="cover">
      <svg class="cover__art" viewBox="0 0 750 1108" role="img" aria-label="Grüne Fläche mit geschwungenen Lichtlinien und Kreismuster">
        <defs>
          <linearGradient id="greenField" x1="0" y1="0" x2="1" y2="1">
            <stop offset="0" stop-color="var(--green-deep)"/>
            <stop offset="0.35" stop-color="var(--green-mid)"/>
            <stop offset="0.7" stop-color="var(--green-light)"/>
            <stop offset="1" stop-color="var(--green-mid)"/>
          </linearGradient>
        </defs>
        <polygon points="0,0 375,0 274,556 371,1108 0,1108" fill="url(#greenField)"/>
      </svg>
      <div class="cover__author">Henrike Lindqvist-Borna</div>
      <h1 class="cover__title"><span>Regen über Glas</span><span>Monde im Moos</span></h1>
      <p class="cover__genre">Roman</p>
    </div>
  </div>
</body>
</html>
```